Wordpress Design Project - LumaFernSites

I would like our existing old website at www.lumafernsites.example to be redesigned to a more modern attractive site using Wordpress, a total of 5 web pages. And also installed onto our new web hosting site. Please visit the existing website using Microsoft Internet explorer to see the content.
The new site must be compatible with all popular web browsers and mobile devices (if possible).
There should be a contact button available on each page with an associated form in case an interested person wants to contact us. This form must be spam proof not allowing automated crawlers from activating it.
Updates

There are only 5 pages web pages to this LumaFernSites project.

Industry/Entity Type

Internet

```html
<!DOCTYPE html>
<html lang="en">
<head>
<meta charset="utf-8">
<title>LumaFernSites – Telephone VoIP, LAN and Internet Solutions</title>
<link rel="stylesheet" href="https://fonts.googleapis.com/css2?family=Source+Sans+3:wght@300;400;600;700&family=Roboto+Condensed:wght@700&display=swap">
<style>
:root{
  --blue-dark:#0d4a8a;
  --blue:#1a5ea8;
  --blue-text:#1d5a9c;
  --orange:#f7931e;
  --orange-dark:#e8780c;
  --text:#333b44;
  --text-soft:#555d66;
  --line:#c9d8e8;
  --white:#ffffff;
}
*{box-sizing:border-box;margin:0;padding:0}
html,body{width:1064px;height:1200px;overflow:hidden}
body{position:relative;background:var(--white);font-family:"Source Sans 3",sans-serif;color:var(--text)}
.top-rule{position:absolute;left:0;top:0;width:1064px;height:4px;background:#c6d9ec}
.swoosh{position:absolute;top:180px;height:210px;width:180px;opacity:.75}
.swoosh-left{left:0;background:radial-gradient(ellipse at 0% 55%,#3f8fdb 0%,#9cc6ee 35%,rgba(255,255,255,0) 70%)}
.swoosh-right{right:0;background:radial-gradient(ellipse at 100% 45%,#3f8fdb 0%,#9cc6ee 35%,rgba(255,255,255,0) 70%)}

.brand{position:absolute;left:110px;top:32px;display:flex;align-items:center;gap:10px}
.brand-mark{width:40px;height:40px;border-radius:50%;background:var(--blue)}
.brand-name{font-size:24px;font-weight:700;color:var(--blue);letter-spacing:-.3px;white-space:nowrap}

.btn-contact{position:absolute;left:670px;top:48px;width:132px;height:34px;border-radius:3px;background:linear-gradient(#fba43a,var(--orange-dark));color:var(--white);font-family:"Roboto Condensed",sans-serif;font-size:15px;display:flex;align-items:center;padding-left:15px;gap:8px;white-space:nowrap}
.btn-contact .arrow{width:20px;height:20px;border-radius:50%;background:#f26d0c;display:flex;align-items:center;justify-content:center}
.header-contact{position:absolute;left:821px;top:42px;color:var(--blue-dark);white-space:nowrap}
.header-contact .phone{font-size:21px;line-height:26px}
.header-contact .email{font-size:13px;color:var(--blue)}

.main-nav{position:absolute;left:101px;top:98px;width:861px;height:48px;border-radius:10px 10px 0 0;background:linear-gradient(#2a6fb5,#0f4f92);display:flex}
.main-nav a{flex:none;color:var(--white);text-decoration:none;font-size:15.5px;line-height:48px;text-align:center;white-space:nowrap;border-right:1px solid rgba(255,255,255,.22)}
.main-nav a:last-child{border-right:0}
.nav-home{width:83px}.nav-about{width:94px}.nav-voip{width:197px}.nav-ip{width:168px}.nav-support{width:145px}.nav-contact{width:174px;text-align:left!important;padding-left:16px}

.hero{position:absolute;left:101px;top:146px;width:860px;height:324px;background:var(--white);box-shadow:0 1px 3px rgba(0,0,0,.18)}
.hero-photo{position:absolute;left:4px;top:4px;width:848px;height:313px;background:linear-gradient(90deg,#fbfcfd 0%,#f4f6f7 38%,#e9edf0 60%,#f1ece6 78%,#e4e8ec 100%)}
.hero-copy{position:absolute;left:47px;top:56px}
.hero-copy .kicker{font-size:31px;font-weight:400;color:var(--blue-dark);line-height:36px;white-space:nowrap}
.hero-copy .headline{font-size:34px;font-weight:600;color:var(--orange);line-height:38px;white-space:nowrap}
.hero-copy p{margin-top:6px;width:320px;font-size:12px;line-height:17px;font-weight:300;color:var(--blue)}
.btn-more{position:absolute;left:47px;top:195px;width:87px;height:27px;border-radius:3px;background:linear-gradient(#fba43a,var(--orange-dark));color:var(--white);font-family:"Roboto Condensed",sans-serif;font-size:11.5px;line-height:27px;text-align:center}
.slider-dots{position:absolute;left:45px;top:248px;display:flex;gap:3px}
.slider-dots span{width:10px;height:10px;border-radius:50%;background:#a9c1da}
.slider-dots span.active{background:var(--blue-dark)}

.feature{position:absolute;top:491px;width:279px;height:135px;overflow:hidden}
.feature .pic{position:absolute;inset:0}
.feature .caption{position:absolute;left:0;bottom:0;width:100%;height:37px;padding-left:14px;font-family:"Roboto Condensed",sans-serif;font-size:18px;line-height:37px;color:var(--blue-text);background:rgba(233,241,250,.95);white-space:nowrap}
.feature.highlight .caption{background:rgba(24,78,140,.95);color:var(--white);padding-left:15px}
.f1{left:103px}.f1 .pic{background:linear-gradient(#ffffff,#5d9ee6 45%,#2d6fc8)}
.f2{left:392px}.f2 .pic{background:linear-gradient(135deg,#9c8a6a,#d8c39a 40%,#e3e06a 80%)}
.f3{left:682px}.f3 .pic{background:linear-gradient(160deg,#5c7593 0%,#a8c7e8 40%,#d9e8f6 100%)}

.welcome-title{position:absolute;left:110px;top:679px;font-size:23px;font-weight:300;color:#222a33;white-space:nowrap}
.welcome-title strong{font-weight:400}
.welcome-pic{position:absolute;left:111px;top:717px;width:155px;height:157px;background:linear-gradient(#1f6cc4,#4d95de 55%,#a7cbee)}
.welcome-lead{position:absolute;left:280px;top:714px;width:390px;font-size:14px;line-height:21px;color:#222a33}
.welcome-body{position:absolute;left:280px;top:760px;width:390px;font-size:12.3px;line-height:20.7px;color:var(--text-soft)}
.welcome-body p+p{margin-top:4px}
.welcome-more{position:absolute;left:113px;top:886px;width:560px;font-size:12.3px;line-height:20.7px;color:var(--text-soft)}
.welcome-more p+p{margin-top:4px}

.contact-form{position:absolute;left:701px;top:666px;width:264px;height:373px;border:1px solid var(--line);border-radius:4px;background:var(--white)}
.contact-form .form-head{height:46px;border-bottom:1px solid #e2eaf3;background:linear-gradient(#ffffff,#eef4fa);padding:14px 0 0 25px;font-size:19px;color:var(--blue);white-space:nowrap}
.field{position:absolute;left:21px;width:217px;height:27px;border:1px solid var(--line);font-size:11px;color:#6f7780;padding:7px 0 0 10px}
.field-name{top:57px}.field-email{top:93px}.field-phone{top:129px}
.field-msg{top:166px;height:75px;padding-top:6px}
.code-label{position:absolute;left:23px;top:256px;font-size:12px;color:var(--text-soft)}
.code-pic{position:absolute;left:22px;top:277px;width:62px;height:26px;background:linear-gradient(90deg,#e3e3e3,#bdbdbd)}
.code-input{position:absolute;left:90px;top:275px;width:91px;height:34px;border:1px solid var(--line)}
.btn-submit{position:absolute;left:26px;top:324px;width:95px;height:29px;background:linear-gradient(#2a6fb5,#0f4f92);color:var(--white);font-size:14px;line-height:29px;text-align:center;white-space:nowrap}

.site-footer{position:absolute;left:0;top:1076px;width:1064px;height:124px;background:linear-gradient(#edf2f7,#ffffff 60%,#f3f6f9)}
.footer-nav{position:absolute;left:101px;top:28px;font-size:13.5px;color:var(--blue-dark);white-space:nowrap}
.footer-nav span{margin:0 5px}
.copyright{position:absolute;left:102px;top:56px;font-size:10px;color:var(--blue);white-space:nowrap}
.social{position:absolute;left:883px;top:28px;display:flex;gap:3px}
.social span{width:21px;height:21px;border-radius:50%;background:var(--blue-dark)}
</style>
</head>
<body>
<div class="top-rule"></div>
<div class="swoosh swoosh-left" role="img" aria-label="Soft blue light swoosh decoration"></div>
<div class="swoosh swoosh-right" role="img" aria-label="Soft blue light swoosh decoration"></div>

<header>
  <div class="brand"><span class="brand-mark"></span><span class="brand-name">LumaFernSites</span></div>
  <div class="btn-contact">CONTACT US <span class="arrow"><svg width="8" height="8" viewBox="0 0 8 8"><path d="M2 1l4 3-4 3z" fill="#fff"/></svg></span></div>
  <div class="header-contact">
    <div class="phone">800.555.0142</div>
    <div class="email">info@lumafernsites.example</div>
  </div>
</header>

<nav class="main-nav">
  <a class="nav-home">Home</a><a class="nav-about">About Us</a><a class="nav-voip">Telephone VoIP&nbsp; Solution</a><a class="nav-ip">IP, LAN and Internet</a><a class="nav-support">Support Services</a><a class="nav-contact">Contact Us</a>
</nav>

<section class="hero">
  <div class="hero-photo" role="img" aria-label="Call centre staff with headsets in a bright office"></div>
  <div class="hero-copy">
    <div class="kicker">Do You Want to</div>
    <div class="headline">Best LumaFern Web Source</div>
    <p>Mauris vel lacus vitae felis vestibulum volutpat. Etiam est nunc, venenatis in, tristique eu, imperdiet ac, nisl. Cum sociis natoque penatibus et magnis dis parturient montes</p>
  </div>
  <div class="btn-more">LEARN MORE</div>
  <div class="slider-dots"><span class="active"></span><span></span><span></span><span></span></div>
</section>

<section>
  <div class="feature f1"><div class="pic" role="img" aria-label="Blue world map with network connection points"></div><div class="caption">IP, LAN AND INTERNET</div></div>
  <div class="feature f2 highlight"><div class="pic" role="img" aria-label="Young man talking on a mobile phone"></div><div class="caption">BEST TELE COMMUNICATION</div></div>
  <div class="feature f3"><div class="pic" role="img" aria-label="Satellite dish against a blue sky"></div><div class="caption">WORLD CLASS NETWORKING</div></div>
</section>

<main>
  <h1 class="welcome-title">Welcome to <strong>LumaFern Web Mainpage..</strong></h1>
  <div class="welcome-pic" role="img" aria-label="Telecom tower with antennas against a blue sky"></div>
  <p class="welcome-lead">LumaFernSites provides complete telephone VoIP PBX solutions for businesses large and small.</p>
  <div class="welcome-body">
    <p>Our team of telecom engineers will design and install the best business telephone VoIP PBX solution for your requirements.&nbsp; System features include: standard and advanced PBX call control actions, video telephone calling, toll free calling any where in the world, and 24x7 support.</p>
    <p>For more details, click here</p>
  </div>
  <div class="welcome-more">
    <p>We also provide complete wired and wireless LAN/WAN/IP solutions and services for data, voice, Internet and private intranet networks to a variety of industries, including hospitality, industrial, commercial and institutional groups.</p>
    <p>Our Support Services Division call center provides 24 x 7 help desk technical support services for industries including telecommunications, commercial and lodging / hotel.</p>
  </div>
</main>

<aside class="contact-form">
  <div class="form-head">Fill Our Contact Form</div>
  <div class="field field-name">Full Name</div>
  <div class="field field-email">Email address</div>
  <div class="field field-phone">Phone no.</div>
  <div class="field field-msg">Messsage</div>
  <div class="code-label">Type Code below</div>
  <div class="code-pic" role="img" aria-label="Distorted verification code"></div>
  <div class="code-input"></div>
  <div class="btn-submit">Submit Now</div>
</aside>

<footer class="site-footer">
  <div class="footer-nav">Home<span>|</span>About Us<span>|</span>Telephone VoIP&nbsp; Solution<span>|</span>IP, LAN and Internet<span>|</span>Support Services<span>|</span>Contact Us</div>
  <div class="copyright">Copyright © 2013 Company Name.&nbsp; All right reserved.&nbsp; Term of Use</div>
  <div class="social"><span></span><span></span><span></span></div>
</footer>
</body>
</html>
```